Design a homepage graphic to show a system journey

We have a software package for parents to update student information and manage school excursions we have attached a concept we like but are open to other ideas so long as they fit the following criteria.
1 It needs to be landscape across the page
2. They are showing a series of processes, each step has its own colour, see below
2.1 The first process is a parent updating their own and students information and approving excursions
2.2 The school then creates and manages the excursion this includes a compliance component
2.3 The school conducts the activity it should show some activity type pictures
2.4 Students return safely to school
3 There can be text boxes within the image to clarify functionality
4. The picture should make anyone watching it understand there is a series of
linked processes the system provides i.e. a journey
There should be the ability to click on each component to link to a specific part of the pager lower down, e.g if the person wanted to look at the school part by clicking on the school it would take them to more information, that information already exists so is not required.
Please review the attached concept diagram and use this a potential guide.
Schools
1 page

```html
<!DOCTYPE html>
<html lang="en">
<head>
<meta charset="utf-8">
<title>School Excursion Journey</title>
<link rel="stylesheet" href="https://fonts.googleapis.com/css2?family=Fjalla+One&family=Pathway+Gothic+One&display=swap">
<style>
:root{
  --ink:#1e1e1e;
  --body:#4a4a4a;
  --line:#8b9a96;
  --sky-top:#cfe2ee;
  --sky-mid:#b9e0d8;
  --field:#a6d8c2;
  --step1:#7b7b7b;--step1-top:#a4a4a4;
  --step2:#7f3305;--step2-top:#b84d0c;
  --step3:#e8824a;--step3-top:#f6a877;
  --step4:#74299a;--step4-top:#9a43c6;
  --step5:#1b57c8;--step5-top:#3f8af0;
  --step6:#0c8593;--step6-top:#2fe0ee;
  --step7:#1a5f34;--step7-top:#2b9c57;
  --step8:#231b18;--step8-top:#54463e;
  --icon-orange:#d06a2c;
  --icon-purple:#6f2d9c;
  --icon-blue:#1553c4;
  --icon-green:#1f6a3c;
}
*{margin:0;padding:0;box-sizing:border-box}
html,body{width:1200px;height:1019px;overflow:hidden}
body{font-family:"Pathway Gothic One",sans-serif;color:var(--body)}
.journey{position:relative;width:1200px;height:1019px;overflow:hidden;
  background:linear-gradient(180deg,var(--sky-top) 0%,var(--sky-mid) 45%,var(--field) 100%)}
.scenery{position:absolute;inset:0;
  background:radial-gradient(ellipse at 85% 75%,rgba(150,190,140,.45),transparent 55%),
             radial-gradient(ellipse at 70% 10%,rgba(255,255,255,.55),transparent 50%)}
.track{position:absolute;left:0;top:0}
.step{position:absolute;text-decoration:none;color:inherit;display:block}
.step-title{font-family:"Fjalla One",sans-serif;color:var(--ink);font-size:24px;line-height:29px;text-transform:uppercase;font-weight:400}
.step-text{font-size:17px;line-height:21.6px;text-align:justify;margin-top:8px}
.icon-slot{position:absolute;border-radius:6px}
.kids-art{position:absolute;left:852px;top:272px;width:348px;height:120px;
  background:linear-gradient(180deg,rgba(255,255,255,0) 0%,rgba(250,200,120,.5) 40%,rgba(110,190,70,.7) 100%);
  border-bottom:3px solid #6dbb45}
.bus-art{position:absolute;left:0;top:788px;width:416px;height:231px;
  background:radial-gradient(ellipse at 35% 55%,#f3c530 0%,#e9b83c 28%,rgba(200,210,170,.8) 55%,rgba(166,216,194,0) 80%)}
</style>
</head>
<body>
<main class="journey">
  <div class="scenery" role="img" aria-label="Soft sky over a green countryside field"></div>

  <svg class="track" width="1200" height="1019" viewBox="0 0 1200 1019" aria-hidden="true">
    <g stroke="var(--line)" stroke-width="1.5" fill="none">
      <line x1="256" y1="340" x2="465" y2="340"/>
      <line x1="448" y1="364" x2="408" y2="408"/>
      <line x1="376" y1="452" x2="626" y2="452"/>
      <line x1="608" y1="474" x2="554" y2="540"/>
      <line x1="518" y1="584" x2="798" y2="584"/>
      <line x1="780" y1="610" x2="714" y2="688"/>
      <line x1="678" y1="734" x2="986" y2="734"/>
    </g>
    <g font-family="Fjalla One, sans-serif" font-size="30" fill="#fff" text-anchor="middle">
      <g><rect x="224" y="316" width="64" height="24" fill="var(--step1)"/><ellipse cx="256" cy="340" rx="32" ry="24" fill="var(--step1)"/><ellipse cx="256" cy="316" rx="32" ry="24" fill="var(--step1-top)"/><text x="256" y="328">01</text></g>
      <g><rect x="432" y="308" width="66" height="32" fill="var(--step2)"/><ellipse cx="465" cy="340" rx="33" ry="25" fill="var(--step2)"/><ellipse cx="465" cy="308" rx="33" ry="25" fill="var(--step2-top)"/><text x="465" y="320">02</text></g>
      <g><rect x="342" y="408" width="68" height="44" fill="var(--step3)"/><ellipse cx="376" cy="452" rx="34" ry="25" fill="var(--step3)"/><ellipse cx="376" cy="408" rx="34" ry="25" fill="var(--step3-top)"/><text x="376" y="420">03</text></g>
      <g><rect x="592" y="398" width="68" height="54" fill="var(--step4)"/><ellipse cx="626" cy="452" rx="34" ry="25" fill="var(--step4)"/><ellipse cx="626" cy="398" rx="34" ry="25" fill="var(--step4-top)"/><text x="626" y="410">04</text></g>
      <g><rect x="483" y="524" width="70" height="60" fill="var(--step5)"/><ellipse cx="518" cy="584" rx="35" ry="26" fill="var(--step5)"/><ellipse cx="518" cy="524" rx="35" ry="26" fill="var(--step5-top)"/><text x="518" y="536">05</text></g>
      <g><rect x="763" y="514" width="70" height="70" fill="var(--step6)"/><ellipse cx="798" cy="584" rx="35" ry="26" fill="var(--step6)"/><ellipse cx="798" cy="514" rx="35" ry="26" fill="var(--step6-top)"/><text x="798" y="526">06</text></g>
      <g><rect x="642" y="646" width="72" height="90" fill="var(--step7)"/><ellipse cx="678" cy="736" rx="36" ry="26" fill="var(--step7)"/><ellipse cx="678" cy="646" rx="36" ry="26" fill="var(--step7-top)"/><text x="678" y="658">07</text></g>
      <g><rect x="950" y="638" width="72" height="98" fill="var(--step8)"/><ellipse cx="986" cy="736" rx="36" ry="26" fill="var(--step8)"/><ellipse cx="986" cy="638" rx="36" ry="26" fill="var(--step8-top)"/><text x="986" y="650">08</text></g>
    </g>
  </svg>

  <div class="kids-art" role="img" aria-label="Illustration of children playing with rackets, a ball, a skipping rope and a frisbee"></div>
  <div class="bus-art" role="img" aria-label="Illustration of a yellow school bus with children boarding beside a stop sign"></div>

  <div class="icon-slot" style="left:42px;top:74px;width:58px;height:78px;background:#5a5a5a;opacity:.8" role="img" aria-label="Parent and child icon"></div>
  <a class="step" href="#parents" style="left:42px;top:168px;width:168px">
    <h2 class="step-title">Parent<br>Information</h2>
    <p class="step-text">Lorem ipsum dolor sinsectetur adipiscing elit,iusmod tempor incididunt ut labore et dolore magna aliqua.</p>
  </a>

  <div class="icon-slot" style="left:350px;top:30px;width:40px;height:72px;background:#b34a0d;opacity:.85" role="img" aria-label="Student carrying books icon"></div>
  <a class="step" href="#students" style="left:350px;top:120px;width:170px">
    <h2 class="step-title">Student<br>Information</h2>
    <p class="step-text">Lorem ipsum dolor sinsectetur adipiscing elit,iusmod tempor incididunt ut labore et dolore magna aliqua.</p>
  </a>

  <div class="icon-slot" style="left:667px;top:160px;width:70px;height:75px;background:var(--icon-purple);opacity:.85" role="img" aria-label="School building icon"></div>
  <a class="step" href="#school" style="left:666px;top:258px;width:200px">
    <h2 class="step-title">The School Manages<br>The Excursion</h2>
    <p class="step-text" style="width:152px">Lorem ipsum dolor sinsectetur adipiscing elit,iusmod tempor incididunt ut labore et dolore magna aliqua.</p>
  </a>

  <svg class="icon-slot" style="left:90px;top:422px" width="64" height="64" viewBox="0 0 64 64" aria-hidden="true">
    <polygon points="32,2 40,8 50,7 53,17 61,23 57,32 61,41 53,47 50,57 40,56 32,62 24,56 14,57 11,47 3,41 7,32 3,23 11,17 14,7 24,8" fill="var(--icon-orange)"/>
    <circle cx="32" cy="32" r="17" fill="none" stroke="#fff" stroke-width="3"/>
    <polyline points="24,32 30,38 41,27" fill="none" stroke="#fff" stroke-width="3.5" stroke-linecap="round" stroke-linejoin="round"/>
  </svg>
  <a class="step" href="#approvals" style="left:172px;top:418px;width:170px">
    <h2 class="step-title">Approving<br>Excursion</h2>
    <p class="step-text">Lorem ipsum dolor sinsectetur adipiscing elit,iusmod tempor incididunt ut labore et dolore magna aliqua.</p>
  </a>

  <a class="step" href="#activity" style="left:878px;top:424px;width:200px">
    <h2 class="step-title">The School Conducts<br>Activity</h2>
    <p class="step-text" style="width:168px">Lorem ipsum dolor sinsectetur adipiscing elit,iusmod tempor incididunt ut labore et dolore magna aliqua.</p>
  </a>

  <svg class="icon-slot" style="left:235px;top:614px" width="66" height="66" viewBox="0 0 66 66" aria-hidden="true">
    <rect x="2" y="2" width="46" height="60" rx="5" fill="var(--icon-blue)"/>
    <g stroke="#fff" stroke-width="4" stroke-linecap="round"><line x1="11" y1="16" x2="38" y2="16"/><line x1="11" y1="27" x2="38" y2="27"/><line x1="11" y1="38" x2="28" y2="38"/><line x1="11" y1="49" x2="26" y2="49"/></g>
    <circle cx="47" cy="47" r="17" fill="var(--icon-blue)" stroke="#fff" stroke-width="3"/>
    <polyline points="39,47 45,53 55,42" fill="none" stroke="#fff" stroke-width="3.5" stroke-linecap="round" stroke-linejoin="round"/>
  </svg>
  <a class="step" href="#compliance" style="left:323px;top:611px;width:200px">
    <h2 class="step-title">The School Accepts<br>All The Update</h2>
    <p class="step-text" style="width:168px">Lorem ipsum dolor sinsectetur adipiscing elit,iusmod tempor incididunt ut labore et dolore magna aliqua.</p>
  </a>

  <div class="icon-slot" style="left:409px;top:782px;width:92px;height:92px;background:var(--icon-green);opacity:.85" role="img" aria-label="Vehicle carrying a group of children icon"></div>
  <a class="step" href="#transport" style="left:526px;top:778px;width:200px">
    <h2 class="step-title">The School Takes The<br>Children To The<br>Excursion</h2>
    <p class="step-text" style="width:168px">Lorem ipsum dolor sinsectetur adipiscing elit,iusmod tempor incididunt ut labore et dolore magna aliqua.</p>
  </a>

  <div class="icon-slot" style="left:824px;top:798px;width:48px;height:74px;background:#1e1e1e;opacity:.85" role="img" aria-label="Student walking with backpack icon"></div>
  <a class="step" href="#return" style="left:890px;top:794px;width:180px">
    <h2 class="step-title">Students Return<br>To The School</h2>
    <p class="step-text" style="width:168px">Lorem ipsum dolor sinsectetur adipiscing elit,iusmod tempor incididunt ut labore et dolore magna aliqua.</p>
  </a>
</main>
</body>
</html>
```